Stationery Design Project

I need a design that is simple, clean and modern, in square style, bold font.
The majority of the design needs to be White and Black with a splash of Red colour.
I would like a design for business cards and letter heads with the following information.
Name, Title, Phone, Fax, Email, Website and company ABN number

Target Market(s)

25 to 65 years old real estate clients

Industry/Entity Type

Business

Requirements
Must have
• All designs must incorporate Company Logo, Name, Title, Phone, Fax, Email, Website and company ABN number

```html
<!DOCTYPE html>
<html lang="en">
<head>
<meta charset="utf-8">
<title>Corvane Real Estate – Business Card</title>
<link rel="stylesheet" href="https://fonts.googleapis.com/css2?family=Source+Sans+3:wght@400;600;700&display=swap">
<style>
  :root {
    --backdrop: #e9e6e2;
    --card: #ffffff;
    --ink: #231f20;
    --ink-soft: #3a3a3a;
    --accent: #d2232a;
    --frame: #1a1a1a;
  }
  * { box-sizing: border-box; margin: 0; padding: 0; }
  html, body { width: 1200px; height: 402px; overflow: hidden; }
  body {
    background: var(--backdrop);
    font-family: "Source Sans 3", "Helvetica Neue", Arial, sans-serif;
    color: var(--ink);
    position: relative;
  }
  .card {
    position: absolute;
    top: 57px;
    width: 512px;
    height: 290px;
    background: var(--card);
    box-shadow: 0 2px 6px rgba(0,0,0,.18);
  }
  .card--front { left: 70px; }
  .card--back { left: 622px; }

  .brand-frame {
    position: absolute;
    border: 4px solid var(--frame);
    border-radius: 14px;
    display: flex;
    flex-direction: column;
    align-items: center;
    justify-content: center;
    text-align: center;
    color: var(--ink);
    font-weight: 700;
    line-height: 1.05;
  }
  .card--front .brand-frame {
    left: 39px; top: 25px; width: 203px; height: 111px;
    font-size: 26px; letter-spacing: .5px;
  }
  .card--back .brand-frame {
    left: 87px; top: 50px; width: 337px; height: 188px;
    font-size: 44px; letter-spacing: 1px;
  }
  .brand-frame .brand-sub {
    font-size: .48em;
    letter-spacing: .35em;
    margin-top: 6px;
  }

  .address {
    position: absolute;
    left: 37px; top: 175px;
    font-size: 12.5px;
    line-height: 13px;
    color: var(--ink-soft);
  }
  .contacts {
    position: absolute;
    left: 37px; top: 217px;
    list-style: none;
    font-size: 13px;
    line-height: 17px;
    color: var(--ink);
  }
  .contacts li { display: flex; align-items: center; gap: 5px; }
  .contacts svg { width: 10px; height: 10px; fill: var(--accent); flex: none; }

  .person {
    position: absolute;
    right: 19px; top: 175px;
    text-align: right;
  }
  .person__name {
    font-size: 15px;
    font-weight: 700;
    color: var(--accent);
  }
  .person__title {
    font-size: 12px;
    color: var(--ink-soft);
    margin-top: 3px;
  }

  .abn {
    position: absolute;
    left: 0; right: 0; top: 249px;
    text-align: center;
    font-size: 18px;
    color: var(--ink);
  }
</style>
</head>
<body>
  <section class="card card--front">
    <div class="brand-frame">
      <span>Corvane</span>
      <span class="brand-sub">Real Estate</span>
    </div>

    <p class="address">Street Name, City Name<br>State, City Zip Code</p>

    <ul class="contacts">
      <li>
        <svg viewBox="0 0 10 10" aria-hidden="true"><path d="M2.2 0.6 L3.8 2.6 L2.9 3.6 C3.5 4.9 5.1 6.5 6.4 7.1 L7.4 6.2 L9.4 7.8 L8.2 9.4 C4.6 9.2 0.8 5.4 0.6 1.8 Z"/></svg>
        123-456-7890
      </li>
      <li>
        <svg viewBox="0 0 10 10" aria-hidden="true"><rect x="2.5" y="0.5" width="5" height="9" rx="1"/></svg>
        123-456-7890
      </li>
      <li>
        <svg viewBox="0 0 10 10" aria-hidden="true"><rect x="0.5" y="2" width="9" height="6.5"/><path d="M0.5 2 L5 5.6 L9.5 2" fill="none" stroke="#fff" stroke-width="0.9"/></svg>
        info@corvane-mail.com
      </li>
      <li>
        <svg viewBox="0 0 10 10" aria-hidden="true"><circle cx="5" cy="5" r="4.6"/><path d="M0.6 5 H9.4" stroke="#fff" stroke-width="0.8"/></svg>
        www.website.com
      </li>
    </ul>

    <div class="person">
      <p class="person__name">Your name</p>
      <p class="person__title">Title</p>
    </div>
  </section>

  <section class="card card--back">
    <div class="brand-frame">
      <span>Corvane</span>
      <span class="brand-sub">Real Estate</span>
    </div>
    <p class="abn">ABN: 123 456 789 00</p>
  </section>
</body>
</html>
```